Recruitment Ad for Social Media Marketing

Ad used to recruit Mortgage Originators

Target Market(s)

Real Estate Agents

Colors

Designer to choose colors to be used in the design.

Requirements
Must have
• HOMEBROKERS
• If you can send a text message, you can earn Mortgage Originator Income too...
• at Brightpath Lending Partners, "If you open the Brightpath door, We'll carry the load"
• We reimburse 100% of Licensing Costs
• * Immediate Payouts
• * Up to 75% Commission Split
• * No Goals or Quotas
• * Manage Your Own Schedule
• * Work from Home
• Send Resume to Careers@brightpathlendmail.com
• Brightpath Lending Partners, Inc.
• 7200 Marlowe Avenue, Ellicott City, MD 21046
• (800) 461-9027 Ext. 23
• NMLS #318764
• (SMALL PRINT AT BOTTOM)
• **Dual income requirements governed by state law. In most cases, Homebrokers cannot serve in a dual capacity for the same transaction.

```html
<!DOCTYPE html>
<html lang="en">
<head>
<meta charset="utf-8">
<title>Brightpath Lending Partners – Mortgage Originator Recruitment</title>
<link rel="stylesheet" href="https://fonts.googleapis.com/css2?family=Oswald:wght@400;500;600&family=Lato:wght@400;700;900&display=swap">
<style>
  :root {
    --page: #c9c9c9;
    --brand-blue: #0a5a9c;
    --khaki: #e3dca0;
    --pill: #d9d4a6;
    --gold: #a8993a;
    --white: #ffffff;
    --ink: #111111;
    --footer: #404040;
  }
  * { margin: 0; padding: 0; box-sizing: border-box; }
  html, body { width: 1200px; height: 1200px; overflow: hidden; background: var(--page); }
  .ad {
    position: absolute; left: 0; top: 136px;
    width: 1232px; height: 952px;
    transform: scale(0.974); transform-origin: top left;
    background: var(--brand-blue);
    overflow: hidden;
    font-family: "Lato", sans-serif;
  }
  .ad-shapes { position: absolute; inset: 0; }
  .headline {
    position: absolute; left: 41px; top: 32px;
    font-family: "Oswald", sans-serif; color: var(--white);
    font-size: 55px; line-height: 58px; font-weight: 400;
    letter-spacing: -0.5px; text-transform: uppercase;
    white-space: nowrap;
  }
  .headline strong { font-weight: 600; }
  .perks {
    position: absolute; top: 184px; list-style: none;
    color: var(--khaki); font-size: 36px; line-height: 43px; font-weight: 400;
  }
  .perks li { position: relative; padding-left: 38px; white-space: nowrap; }
  .perks li::before { content: "•"; position: absolute; left: 0; font-size: 26px; }
  .perks-left { left: 42px; }
  .perks-right { left: 455px; }
  .resume-pill {
    position: absolute; left: 0; top: 352px; width: 806px; height: 83px;
    background: var(--pill); border-radius: 0 42px 42px 0;
    box-shadow: 0 14px 18px -10px rgba(0,0,0,0.45);
    font-family: "Oswald", sans-serif; font-weight: 500; font-size: 36px;
    color: var(--ink); line-height: 83px; padding-left: 42px; white-space: nowrap;
  }
  .reimburse {
    position: absolute; left: 835px; top: 219px; width: 390px; height: 390px;
    border-radius: 50%; background: var(--gold);
    box-shadow: 0 0 0 13px var(--white);
    color: var(--white); font-family: "Oswald", sans-serif; text-align: center;
    text-transform: uppercase;
  }
  .reimburse .line-top { position: absolute; top: 98px; width: 100%; font-size: 54px; line-height: 56px; font-weight: 500; }
  .reimburse .figure { position: absolute; top: 146px; left: 48px; font-size: 118px; line-height: 110px; font-weight: 600; letter-spacing: -4px; }
  .reimburse .figure small { font-size: 40px; letter-spacing: 0; margin-left: 6px; }
  .reimburse .line-bottom { position: absolute; top: 254px; width: 100%; font-size: 48px; line-height: 50px; font-weight: 500; }
  .team-photo {
    position: absolute; left: -30px; top: 505px; width: 420px; height: 420px;
    background: var(--white); border: 3px solid #9a9a9a;
    transform: rotate(-12deg);
    box-shadow: 8px 10px 16px rgba(0,0,0,0.4);
    padding: 16px;
  }
  .team-photo .fill { width: 100%; height: 100%; background: linear-gradient(160deg, #3a3a3a, #111111); border: 2px solid #6a6a6a; }
  .housing-badge { position: absolute; left: 704px; top: 644px; width: 150px; height: 160px; background: var(--ink); }
  .brand {
    position: absolute; left: 895px; top: 650px; width: 300px;
    color: var(--brand-blue); font-weight: 700; text-align: center;
  }
  .brand .mark { width: 54px; height: 54px; border-radius: 50%; background: var(--gold); margin: 0 auto 10px; }
  .brand .name { font-size: 17px; line-height: 22px; white-space: nowrap; }
  .brand .tagline { font-size: 12px; line-height: 16px; margin-top: 6px; }
  .contact {
    position: absolute; left: 0; top: 820px; width: 100%; height: 132px;
    background: var(--footer); color: var(--white);
  }
  .contact .address { position: absolute; left: 540px; top: 14px; font-size: 24px; white-space: nowrap; }
  .contact .phone { position: absolute; left: 540px; top: 44px; font-size: 38px; font-weight: 900; white-space: nowrap; }
  .contact .nmls { font-size: 20px; font-weight: 700; margin-left: 22px; }
  .contact .icon { position: absolute; left: 506px; fill: var(--white); }
  .contact .fine-print { position: absolute; left: 508px; top: 94px; width: 680px; font-size: 13px; line-height: 15px; }
</style>
</head>
<body>
<main class="ad">
  <svg class="ad-shapes" viewBox="0 0 1232 952" width="1232" height="952" aria-hidden="true">
    <defs>
      <linearGradient id="swoosh" x1="0" y1="1" x2="1" y2="0">
        <stop offset="0" stop-color="#0a5a9c"/>
        <stop offset="1" stop-color="#c7dcef"/>
      </linearGradient>
    </defs>
    <path d="M470 820 C520 700 600 610 760 600 C880 592 1000 560 1100 500 C1180 440 1220 360 1232 270 L1232 952 L470 952 Z" fill="url(#swoosh)"/>
    <path d="M535 820 C590 700 690 620 820 605 C950 590 1060 550 1130 490 C1195 430 1225 350 1232 286 L1232 952 L535 952 Z" fill="#ffffff"/>
  </svg>

  <h1 class="headline"><strong>If you can send a text message,</strong> you can earn<br>mortgage originator income too......</h1>

  <ul class="perks perks-left">
    <li>Immediate Payouts</li>
    <li>No Goals or Quotas</li>
    <li>Work from Home</li>
  </ul>
  <ul class="perks perks-right">
    <li>Up to 75% Commission Split</li>
    <li>Manage Your Own<br>Schedule</li>
  </ul>

  <div class="resume-pill">Send Resume to Careers@brightpathlendmail.com</div>

  <div class="reimburse">
    <div class="line-top">We reimburse</div>
    <div class="figure">100%<small>of</small></div>
    <div class="line-bottom">Licensing costs</div>
  </div>

  <div class="team-photo"><div class="fill" role="img" aria-label="Silhouettes of a group of people jumping with arms raised in celebration"></div></div>

  <div class="housing-badge" role="img" aria-label="Equal housing opportunity badge"></div>

  <div class="brand">
    <div class="mark"></div>
    <div class="name">Brightpath Lending Partners, Inc.</div>
    <div class="tagline">"If you open the Brightpath door,<br>We'll carry the load"</div>
  </div>

  <footer class="contact">
    <svg class="icon" style="top:16px" width="22" height="28" viewBox="0 0 22 28" aria-hidden="true"><path d="M11 0C5 0 1 4.5 1 10c0 7 10 18 10 18s10-11 10-18C21 4.5 17 0 11 0zm0 14a4 4 0 1 1 0-8 4 4 0 0 1 0 8z"/></svg>
    <div class="address">7200 Marlowe Avenue, Ellicott City, MD 21046</div>
    <svg class="icon" style="top:56px" width="26" height="28" viewBox="0 0 24 24" aria-hidden="true"><path d="M6.6 10.8a15.1 15.1 0 0 0 6.6 6.6l2.2-2.2c.3-.3.7-.4 1-.2 1.1.4 2.3.6 3.6.6.6 0 1 .4 1 1V20c0 .6-.4 1-1 1A17 17 0 0 1 3 4c0-.6.4-1 1-1h3.5c.6 0 1 .4 1 1 0 1.3.2 2.5.6 3.6.1.3 0 .7-.2 1z"/></svg>
    <div class="phone">(800) 461-9027 Ext. 23<span class="nmls">NMLS #318764</span></div>
    <p class="fine-print">Dual income requirements governed by state law. In most cases, Homebrokers cannot serve in a dual capacity for the same transaction.</p>
  </footer>
</main>
</body>
</html>
```